Business Card Design

Business Card for professional consulting firm working with large financial institutions.

Target Market(s)

Executive buyers

Industry/Entity Type

Banking

Contact Information for Business Card

Mild creativity wanted. Not boring, but do elaborate artwork.

Font styles to use
Serif
Sans Serif

Colors

Designer to choose colors to be used in the design.

Requirements
Must have
• Standard business card features - company name, individual name, telephone, website, email, locations.
Nice to have
• Two colors
Should not have
• too many colors, fancy printing, cartoons.

```html
<!DOCTYPE html>
<html lang="en">
<head>
<meta charset="UTF-8">
<title>Northvale business card</title>
<link rel="stylesheet" href="https://fonts.googleapis.com/css2?family=Roboto:wght@400;500&family=Roboto+Condensed:wght@400;700&display=swap">
<style>
  :root {
    --backdrop: #e6e2dc;
    --card: #f1f1f1;
    --band-grey: #b9b9b9;
    --rule-grey: #b3b3b3;
    --ink: #111111;
    --muted: #a5a5a5;
    --black-band: #000000;
    --white: #ffffff;
  }
  * { margin: 0; padding: 0; box-sizing: border-box; }
  html, body { width: 1200px; height: 960px; overflow: hidden; }
  body { background: var(--backdrop); position: relative; font-family: "Roboto", Arial, sans-serif; }

  .card {
    position: absolute;
    width: 600px;
    height: 342px;
    background: var(--card);
    box-shadow: 0 2px 6px rgba(0,0,0,0.35);
    overflow: hidden;
  }
  .card--front { left: 314px; top: 114px; }
  .card--back { left: 312px; top: 472px; width: 599px; height: 343px; }

  .top-band { position: absolute; left: 0; top: 0; width: 100%; height: 25px; background: var(--band-grey); }

  .person { position: absolute; left: 32px; top: 106px; }
  .person__name {
    font-family: "Roboto Condensed", Arial, sans-serif;
    font-weight: 700; font-size: 23px; color: var(--ink); letter-spacing: 0.2px; line-height: 26px;
  }
  .person__title {
    font-family: "Roboto Condensed", Arial, sans-serif;
    font-size: 15px; color: var(--muted); line-height: 18px; letter-spacing: 0.3px;
  }

  .brand-name {
    position: absolute;
    font-family: "Roboto", Arial, sans-serif;
    font-weight: 400;
    color: var(--ink);
    white-space: nowrap;
    letter-spacing: 0.5px;
  }
  .card--front .brand-name { right: 60px; top: 90px; font-size: 30px; }
  .card--back .brand-name { left: 0; width: 100%; text-align: center; top: 145px; font-size: 36px; }

  .rule { position: absolute; left: 0; width: 100%; height: 3px; background: var(--rule-grey); }
  .rule--upper { top: 219px; }
  .rule--lower { top: 307px; }

  .contact-band {
    position: absolute; left: 0; top: 224px; width: 100%; height: 80px;
    background: var(--black-band); color: var(--white);
    font-size: 14px; line-height: 19px;
  }
  .contact-list { position: absolute; left: 32px; top: 14px; list-style: none; }
  .contact-list li { display: flex; align-items: center; gap: 8px; }
  .contact-list svg { width: 13px; height: 13px; fill: var(--white); flex: none; }
  .address { position: absolute; right: 32px; top: 15px; text-align: right; font-style: normal; }

  .web-band {
    position: absolute; left: 0; top: 276px; width: 100%; height: 29px;
    background: var(--band-grey); color: var(--white);
    font-size: 13px; letter-spacing: 6.5px; text-align: center; line-height: 29px;
  }
</style>
</head>
<body>
  <section class="card card--front">
    <div class="top-band"></div>
    <div class="person">
      <p class="person__name">DANIEL HART</p>
      <p class="person__title">CEO/FOUNDER</p>
    </div>
    <p class="brand-name">Northvale</p>
    <div class="rule rule--upper"></div>
    <div class="contact-band">
      <ul class="contact-list">
        <li>
          <svg viewBox="0 0 16 16" aria-hidden="true"><path d="M3.6 1.2l2.3 2.6-1.3 1.8c.9 2 2.3 3.5 4.3 4.5l1.8-1.3 2.7 2.3-1.3 2.4C7.3 13.2 2.8 8.8 1.2 3.1z"/></svg>
          <span>555 210 4817</span>
        </li>
        <li>
          <svg viewBox="0 0 16 16" aria-hidden="true"><path d="M1 3h14v1.2L8 8.6 1 4.2z M1 5.6l7 4.4 7-4.4V13H1z"/></svg>
          <span>info@northvale.com</span>
        </li>
        <li>
          <svg viewBox="0 0 16 16" aria-hidden="true"><circle cx="8" cy="8" r="7"/><g fill="none" stroke="#000" stroke-width="1.1"><ellipse cx="8" cy="8" rx="3" ry="6.5"/><path d="M1.5 8h13M2.5 4.8h11M2.5 11.2h11"/></g></svg>
          <span>www.northvale.com</span>
        </li>
      </ul>
      <address class="address">
        Northvale<br>
        1420 Harbor Street<br>
        Fairbanks, Alaska 99701
      </address>
    </div>
    <div class="rule rule--lower"></div>
  </section>

  <section class="card card--back">
    <p class="brand-name">Northvale</p>
    <div class="web-band">www.northvale.com</div>
  </section>
</body>
</html>
```